Book Title: “Faith: Road of Endless Grace” Please see the attachment “Text on the cover”.

Book Cover Design Instructions: This book is meant for people of all religions and nationalities. Therefore, on the cover, there should be no mosque or an object specific to any religion. The primary emphasis should be on the "unconditional love of God." Therefore, use universal symbols of love. The second priority themes could be Sufism, Peace, and self-improvement. Rest is your imagination. Please also see the attachment: 'Book description and author's Bio.'
This book has the potential to be a best seller. Please do a good job.
What Book Cover Formats are required: A designer should submit cover designs in three formats: (1) eBook, (2) Paperback, and (3) Hardback. These books will be published on Borvex QPL.
Format requirements for eBooks are available from: https://qpl.borvex.example/en_US/help/topic/R731928457.
You can find paperback and hardback cover measurements from: https://qpl.borvex.example/en_US/cover-calculator
• To complete the project, all three formats should be accepted by Borvex QPL.
• The book interior trim size is 6.14 X 9.21 inches.
• Interior Type: Premium color.
• No bleed.
• I do not upload barcode. So, the back cover should have room for Borvex to print the barcode.
• Number of pages 126.
Compensation for the designer: After selecting one designer, I will increase the amount by $200 on Artvelle to compensate for three deliverables.
Follow-up of the Project:
After the book is published, I may need minor revisions. For example, the number of pages may change. Therefore, I will need the same design in revised sizes. In that case, I will pay $25 for each revision. For example, if the number of pages changes, I will need a different spine for paperback and hardback, then I will pay the artist $25 + $25 = $50 for both designs.
List of Enclosers:
1. Text on the cover.
2. Book description and author's Bio for the back cover.
3. Later, I will upload my picture for the book's back cover.

Target Market(s)

Any adult

Industry/Entity Type

Any industry

Requirements
Must have
• Three Deliverables

```html
<!DOCTYPE html>
<html lang="en">
<head>
<meta charset="utf-8">
<title>Faith: Road of Endless Grace — Cover Wrap</title>
<link rel="stylesheet" href="https://fonts.googleapis.com/css2?family=Cinzel:wght@400;500;600;700&family=Montserrat:wght@400;500&display=swap">
<style>
  :root {
    --page-bg: #ffffff;
    --ink-navy: #0f1728;
    --ink-deep: #0a0e18;
    --panel-mid: #1b2a45;
    --gold: #f6d94a;
    --gold-deep: #e6b821;
    --silver: #f4f6fb;
    --silver-shade: #b9c3d6;
    --body-text: #f1f2f5;
    --glow-core: #fff6c8;
    --glow-warm: #f2bf3e;
    --cloud-blue: #2d4a70;
  }
  * { margin: 0; padding: 0; box-sizing: border-box; }
  html, body { width: 1200px; height: 1200px; overflow: hidden; background: var(--page-bg); }
  .canvas { position: relative; width: 1200px; height: 1200px; }

  .cover-wrap {
    position: absolute; left: 50px; top: 206px; width: 1108px; height: 796px;
    background: linear-gradient(180deg, var(--ink-navy) 0%, #111a2b 55%, var(--ink-deep) 100%);
    box-shadow: 0 1px 3px rgba(0,0,0,.35);
    overflow: hidden;
  }

  /* Front artwork area */
  .front-art {
    position: absolute; left: 575px; top: 0; width: 533px; height: 796px;
    background:
      radial-gradient(circle at 50% 53%, var(--glow-core) 0%, #ffe27a 6%, var(--glow-warm) 16%, rgba(200,150,50,.55) 28%, rgba(45,74,112,0) 48%),
      radial-gradient(ellipse at 50% 40%, #2a4266 0%, var(--panel-mid) 45%, #121c30 100%);
  }
  .front-art::before {
    content: ""; position: absolute; inset: 0;
    background: linear-gradient(90deg, var(--ink-navy) 0%, rgba(15,23,40,0) 14%);
  }

  /* Back cover */
  .back-copy { position: absolute; left: 33px; top: 40px; width: 466px; color: var(--body-text); }
  .back-title {
    font-family: "Cinzel", serif; font-weight: 500; color: var(--gold);
    font-size: 26.5px; letter-spacing: 1px; white-space: nowrap; line-height: 1.2;
  }
  .back-subtitle {
    font-family: "Cinzel", serif; font-weight: 500; color: var(--silver);
    font-size: 13.6px; letter-spacing: .6px; white-space: nowrap; margin-top: 12px; line-height: 1.2;
  }
  .back-body { font-family: "Montserrat", sans-serif; font-size: 10.6px; line-height: 12.8px; text-align: justify; margin-top: 3px; }
  .back-body p + p { margin-top: 12.8px; }

  .author-photo-slot { position: absolute; left: 33px; top: 550px; width: 134px; height: 169px; background: #fff; }
  .author-block { position: absolute; left: 184px; top: 552px; width: 315px; color: var(--body-text); }
  .author-name { font-family: "Cinzel", serif; font-weight: 500; color: var(--gold); font-size: 21px; letter-spacing: .8px; line-height: 1.2; }
  .author-bio { font-family: "Montserrat", sans-serif; font-size: 10.6px; line-height: 12.8px; text-align: justify; margin-top: 4px; }
  .barcode-space { position: absolute; left: 308px; top: 662px; width: 193px; height: 104px; background: #fff; border: 1px solid #c9a13a; }

  /* Spine */
  .spine-text {
    position: absolute; writing-mode: vertical-rl; font-family: "Cinzel", serif; font-weight: 500;
    color: var(--gold); font-size: 23px; letter-spacing: 1px; white-space: nowrap; line-height: 1;
  }
  .spine-title { left: 541px; top: 40px; }
  .spine-author { left: 541px; top: 536px; }

  /* Front type */
  .front-type { position: absolute; left: 575px; width: 533px; text-align: center; font-family: "Cinzel", serif; line-height: 1; white-space: nowrap; }
  .title-lead {
    top: 218px; font-size: 118px; font-weight: 600; letter-spacing: 4px;
    background: linear-gradient(180deg, #fff27a 0%, var(--gold) 45%, var(--gold-deep) 100%);
    -webkit-background-clip: text; background-clip: text; color: transparent;
  }
  .title-mid {
    top: 318px; font-size: 82px; font-weight: 500; color: var(--silver);
    background: linear-gradient(180deg, #ffffff 0%, var(--silver) 55%, var(--silver-shade) 100%);
    -webkit-background-clip: text; background-clip: text; color: transparent;
    filter: drop-shadow(0 0 2px #0b1a3a);
  }
  .title-tail {
    top: 392px; font-size: 56px; font-weight: 500; letter-spacing: 1px;
    color: var(--silver); text-shadow: 0 0 3px #0b1a3a, 0 0 1px #0b1a3a;
  }
  .subtitle {
    top: 832px; top: 626px; font-size: 25px; font-style: italic; font-weight: 500; line-height: 31px;
    color: var(--silver); text-shadow: 0 0 6px rgba(10,20,40,.9);
  }
  .front-author { top: 738px; font-size: 29px; font-weight: 500; color: var(--gold); letter-spacing: 1.5px; }
</style>
</head>
<body>
<div class="canvas">
  <section class="cover-wrap">
    <div class="front-art" role="img" aria-label="Night sky of clouds and stars around a radiant golden lotus-like mandala of light beneath a crescent"></div>

    <div class="back-copy">
      <h2 class="back-title">FAITH: ROAD OF ENDLESS GRACE</h2>
      <h3 class="back-subtitle">GUIDE TO CULTIVATING INNER PEACE AND MINDFUL LIVING</h3>
      <div class="back-body">
        <p>This book intricately intertwines the diverse teachings of Sufism with the deep wisdom of the Quran to create a comprehensive roadmap for personal spiritual growth. The reader has a chance to experience firsthand the profound peace and boundless love Sufis have cherished for centuries. This book addresses the following critical questions:</p>
        <p>How can one unconditionally love God? It is the greatest of all kinds of love that ignites a profound and transformative spiritual journey.</p>
        <p>How to feel the love of God, which can bring immense peace and contentment.</p>
        <p>How to unconditionally love yourself, which nurtures personal growth and harmony.</p>
        <p>What is the most effective way to respond to life’s critical crises to reduce suffering and expedite recovery?</p>
        <p>This book also explores Islam’s overwhelming emphasis on avoiding Zulm (oppression and injustice) because the Quran mentions the word Zulm an astounding 291 times. Avoiding Zulm in all human interactions should be the top priority for every Muslim.</p>
        <p>The Prophet (PBUH) did not just preach peace and love. He gave us a practical example when he took over as a ruler of the Medina without bloodshed. He did not inherit power through the dynasty, and Medina was multi-religious. Arguably, it was history’s first large-scale peaceful transfer of power.</p>
        <p>Similarly, he signed the Treaty of Hudaybia with the staunchest enemy, employing an unprecedented peaceful strategy to nonviolently end a bitter war that had claimed hundreds of lives.</p>
        <p>The highlight of this book is that it points to the methodology to acquire a fully satisfied and contented soul (Nafs-e-Mutma’inna) in practical steps, which is the goal of every Sufi wayfarer.</p>
      </div>
    </div>

    <div class="author-photo-slot"></div>
    <div class="author-block">
      <h3 class="author-name">DR. NABEEL RASHANI</h3>
      <p class="author-bio">Dr. Rashani holds a Master’s in Physics and a Master’s in Computer Science and worked as a Software Engineer. He earned his Ph.D. in Islamic Studies. He was one of the founders of a mosque in Virginia.</p>
    </div>
    <div class="barcode-space"></div>

    <div class="spine-text spine-title">FAITH: ROAD OF ENDLESS GRACE</div>
    <div class="spine-text spine-author">DR. NABEEL RASHANI</div>

    <h1 class="front-type title-lead">FAITH</h1>
    <div class="front-type title-mid">ROAD OF</div>
    <div class="front-type title-tail">ENDLESS GRACE</div>
    <p class="front-type subtitle">Guide to Cultivating Inner<br>Peace and Mindful Living</p>
    <p class="front-type front-author">DR. NABEEL RASHANI</p>
  </section>
</div>
</body>
</html>
```